Harborview Estates Business Card for Apartment Buildings

Create business cards for resident managers who run apartment buildings. The audience is the public who are searching for apartment rentals, and current residents who live at the apartment building. Key design element will be incorporating the company logo, however, the logo cannot dominate. The building name and manager name are more important than the logo. Current business card design leaves little room for copy, so we may need to reduce the size on the current card to allow for more space for copy.

Target Market(s)

Adults 18-65 years of age, who are looking for an apartment rental, plus current residents who live at our apartment buildings.

Industry/Entity Type

Property Management

Contact Information for Business Card

A major design element will be use of the company logo. Important property and manager contact information must be part of the design. The size of the logo will need to be reduced to make room for building and manager contact copy.

Font styles to use
Sans Serif

Colors
3176b5
000000
959595
ffffff

Requirements
Must have
• 1) Incorporate the company logo.
• 2) Use the company colors (dark blue, black/grey, over white).
• 3) FEATURE THE BUILDING NAME
• 4) FEATURE THE MANAGER NAME
• 5) The company name is less important than BUILDING and MANAGER
• 6) Manager contact information
• **SEE ATTACHED CREATIVE BRIEF**
Nice to have
• 1) Back of card logo watermark
• 2) Ability to write notes on back of carfd
Should not have
• Avoid letting the company logo dominate the card, the building name and manager are more important than the company logo.

```html
<!DOCTYPE html>
<html lang="en">
<head>
<meta charset="utf-8">
<title>Harborview Estates – Business Card</title>
<link rel="stylesheet" href="https://fonts.googleapis.com/css2?family=Roboto:wght@400;700&display=swap">
<style>
  :root {
    --backdrop: #3b3c3e;
    --card: #1f2022;
    --brand-blue: #1e8ad6;
    --band-start: #1b6fb3;
    --band-end: #0f5c9a;
    --white: #ffffff;
    --muted: #e6e6e6;
  }
  * { margin: 0; padding: 0; box-sizing: border-box; }
  html, body { width: 799px; height: 1200px; overflow: hidden; }
  body {
    background: var(--backdrop);
    font-family: "Roboto", Arial, sans-serif;
    position: relative;
  }
  .card {
    position: absolute;
    left: 80px;
    width: 640px;
    height: 366px;
    background: var(--card);
    border-radius: 4px;
    box-shadow: 0 14px 30px rgba(0,0,0,0.45);
    overflow: hidden;
  }
  .card--front { top: 150px; }
  .card--back { top: 690px; }

  /* Front */
  .front-wordmark {
    position: absolute;
    left: 0; right: 0; top: 140px;
    text-align: center;
    color: var(--brand-blue);
    font-weight: 700;
    font-size: 40px;
    letter-spacing: 1px;
    line-height: 1.1;
  }
  .front-wordmark .wordmark-line2 {
    display: block;
    font-size: 22px;
    letter-spacing: 6px;
    margin-top: 6px;
  }

  /* Back */
  .back-wordmark {
    position: absolute;
    left: 150px; top: 34px;
    color: var(--brand-blue);
    font-weight: 700;
    font-size: 30px;
    line-height: 1.05;
    letter-spacing: 0.5px;
  }
  .back-wordmark .wordmark-line2 {
    display: block;
    font-size: 15px;
    letter-spacing: 4px;
    margin-top: 4px;
  }
  .name-band {
    position: absolute;
    left: 0; right: 0;
    top: 118px;
    height: 84px;
    background: linear-gradient(90deg, var(--band-start), var(--band-end) 70%, var(--brand-blue));
  }
  .manager-name {
    position: absolute;
    left: 60px; top: 10px;
    color: var(--white);
    font-weight: 700;
    font-size: 34px;
  }
  .manager-title {
    position: absolute;
    left: 60px; top: 52px;
    color: var(--muted);
    font-size: 18px;
  }
  .contact-list {
    position: absolute;
    left: 40px; top: 232px;
    list-style: none;
  }
  .contact-list li {
    display: flex;
    align-items: center;
    gap: 12px;
    color: var(--white);
    font-size: 17px;
    height: 26px;
  }
  .contact-list svg { width: 14px; height: 14px; flex: none; }
</style>
</head>
<body>

<section class="card card--front" aria-label="Card front">
  <div class="front-wordmark">HARBORVIEW<span class="wordmark-line2">ESTATES LLC</span></div>
</section>

<section class="card card--back" aria-label="Card back">
  <div class="back-wordmark">HARBORVIEW<span class="wordmark-line2">ESTATES LLC</span></div>

  <div class="name-band">
    <div class="manager-name">Dana Whitfield</div>
    <div class="manager-title">Property Manager</div>
  </div>

  <ul class="contact-list">
    <li>
      <svg viewBox="0 0 16 16" aria-hidden="true"><circle cx="8" cy="8" r="7" fill="none" stroke="#1e8ad6" stroke-width="1.5"/><path d="M5.5 4.5l1.5 1.5-1 1a5 5 0 0 0 3 3l1-1 1.5 1.5-1 1.2c-3 0-6-3-6-6z" fill="#1e8ad6"/></svg>
      <span>555-014-2287</span>
    </li>
    <li>
      <svg viewBox="0 0 16 16" aria-hidden="true"><rect x="4" y="1.5" width="8" height="4" fill="#1e8ad6"/><rect x="1.5" y="5.5" width="13" height="6" rx="1" fill="#1e8ad6"/><rect x="4" y="10" width="8" height="4.5" fill="#1f2022" stroke="#1e8ad6" stroke-width="1.2"/></svg>
      <span>555-014-3390</span>
    </li>
    <li>
      <svg viewBox="0 0 16 16" aria-hidden="true"><rect x="1.5" y="3.5" width="13" height="9" fill="none" stroke="#1e8ad6" stroke-width="1.5"/><path d="M1.5 3.5L8 9l6.5-5.5" fill="none" stroke="#1e8ad6" stroke-width="1.5"/></svg>
      <span>dana@harborviewestates.us</span>
    </li>
    <li>
      <svg viewBox="0 0 16 16" aria-hidden="true"><circle cx="8" cy="8" r="6.5" fill="none" stroke="#1e8ad6" stroke-width="1.4"/><ellipse cx="8" cy="8" rx="3" ry="6.5" fill="none" stroke="#1e8ad6" stroke-width="1.2"/><path d="M1.5 8h13" stroke="#1e8ad6" stroke-width="1.2"/></svg>
      <span>www.harborviewestates.us</span>
    </li>
  </ul>
</section>

</body>
</html>
```